The Brandwell Firm

We need a new design for our letterhead and envelopes. We are a personal injury and criminal defense firm so we need something modern and clean, but more on the professional/traditional side. Our new logo has two colors and is attached to the file so we need something that works well with those colors/matches the design. The following information needs to be on the letterhead:
Phone: (555) 214-3370
Fax: (555) 214-5186
Toll-Free: (888) 431-2059
Post Office Box 4721
Millbrook, SC 29555-4721
HarmClaimCounsel.example
PalmettoTrialAdvocates.example

Target Market(s)

Clients, government agencies, other law firms

Industry/Entity Type

Legal

Font styles to use
Sans Serif
Other font styles liked:
• Arial

Colors

Designer to choose colors to be used in the design.

Requirements
Must have
• Must look professional and clean, modern
Nice to have
• I would like to see a design that works with the logo but does not distract from the content that will be printed on it
Should not have
• Too many colors or crazy designs.

```html
<!DOCTYPE html>
<html lang="en">
<head>
<meta charset="utf-8">
<title>The Brandwell Firm — Stationery</title>
<link href="https://fonts.googleapis.com/css2?family=Lato:wght@400;700&display=swap" rel="stylesheet">
<style>
  :root {
    --backdrop: #b9b9b9;
    --paper: #ffffff;
    --ink: #555555;
    --ink-soft: #6a6a6a;
    --brand-blue: #2e3192;
    --brand-red: #d2232a;
    --flap: #45469a;
  }
  * { margin: 0; padding: 0; box-sizing: border-box; }
  html, body { width: 1200px; height: 810px; overflow: hidden; }
  body {
    background: var(--backdrop);
    font-family: "Lato", Arial, sans-serif;
    color: var(--ink);
    position: relative;
  }
  .letterhead, .envelope {
    position: absolute;
    background: var(--paper);
  }
  .letterhead { left: 146px; top: 106px; width: 436px; height: 612px; }
  .envelope { left: 638px; width: 444px; height: 221px; }
  .envelope--back { top: 194px; }
  .envelope--front { top: 444px; height: 220px; }

  .wordmark {
    position: absolute;
    font-weight: 700;
    font-size: 21px;
    line-height: 1.1;
    color: var(--brand-blue);
    display: flex;
    align-items: center;
    gap: 8px;
  }
  .wordmark__dot {
    width: 12px; height: 12px; border-radius: 50%;
    background: var(--brand-red);
    flex: none;
  }
  .letterhead .wordmark { left: 38px; top: 62px; }
  .envelope--front .wordmark { left: 16px; top: 44px; }

  .contact {
    position: absolute; left: 308px; top: 56px;
    font-size: 7.4px; line-height: 9.6px; color: var(--ink);
  }
  .contact__lines { margin-top: 6px; display: grid; grid-template-columns: 32px 6px auto; }
  .contact__label { color: var(--brand-blue); font-weight: 700; }

  .recipient {
    position: absolute; left: 38px; top: 204px;
    font-size: 8px; line-height: 11.4px; color: var(--ink-soft);
  }
  .body-copy {
    position: absolute; left: 38px; width: 362px;
    font-size: 7.9px; line-height: 11.4px; text-align: justify; color: var(--ink-soft);
  }
  .body-copy--first { top: 268px; }
  .body-copy--second { top: 371px; }

  .signature {
    position: absolute; left: 38px; top: 436px; width: 86px; height: 58px;
    background: linear-gradient(135deg, #eef0f8, #dfe1f0);
    border-radius: 4px;
  }
  .signatory {
    position: absolute; left: 38px; top: 504px;
    font-size: 8px; color: var(--ink-soft);
  }
  .footer-links {
    position: absolute; left: 0; right: 0; top: 584px;
    text-align: center; font-size: 8px; color: var(--ink);
  }
  .footer-links__sep { color: var(--brand-blue); font-weight: 700; margin: 0 5px; }

  .envelope__flap { position: absolute; left: 0; top: 0; width: 444px; height: 66px; }
  .envelope__return {
    position: absolute; left: 42px; top: 102px;
    font-size: 7.4px; line-height: 9.4px; color: var(--ink);
  }
</style>
</head>
<body>

<section class="letterhead">
  <div class="wordmark"><span class="wordmark__dot"></span>The Brandwell Firm</div>

  <div class="contact">
    <p>Post Office Box 4721</p>
    <p>Millbrook, SC 29555-4721</p>
    <div class="contact__lines">
      <span class="contact__label">Phone</span><span>:</span><span>(555) 214-3370</span>
      <span class="contact__label">Fax</span><span>:</span><span>(555) 214-5186</span>
      <span class="contact__label">Toll-Free</span><span>:</span><span>(888) 431-2059</span>
    </div>
  </div>

  <div class="recipient">
    <p>Dear Hallorin</p>
    <p>KTV Print Works Corporation</p>
    <p>Department Design</p>
  </div>

  <p class="body-copy body-copy--first">Lorem ipsum dolor sit amet, consectetuer adipiscing elit. Aenean commodo ligula eget dolor. Aenean massa. Cum sociis natoque penatibus et magnis dis parturient montes, nascetur ridiculus mus. Donec quam felis, ultricies nec, pellentesque eu, pretium quis, sem. Nulla consequat massa quis enim. Donec pede justo, fringilla vel, aliquet nec, vulputate eget, arcu. In enim justo, rhoncus ut, imperdiet a, venenatis vitae, justo. Nullam dictum felis eu pede mollis pretium. Integer tincidunt. Cras dapibus. Vivamus elementum semper nisi.Nullam dictum felis eu pede mollis pretium. Integer tincidunt. Cras dapibus. Vivamus elementum semper nisi.felis eu pede mollis pretium. Integer tincidunt. Cras dapibus.</p>

  <p class="body-copy body-copy--second">Quisque rutrum. Aenean imperdiet. Etiam ultricies nisi vel augue. Curabitur ullamcorper ultricies nisi. Nam eget dui. Etiam rhoncus. Maecenas tempus, tellus eget condimentum rhoncus, sem quam semper libero, sit amet adipiscing sem neque sed ipsum.felis pede mollis pretium. I am tincidunt. Cras dapibus.</p>

  <div class="signature" role="img" aria-label="Handwritten signature of the director"></div>
  <p class="signatory">Director/Excecutive Director</p>

  <p class="footer-links">www.HarmClaimCounsel.example<span class="footer-links__sep">|</span>www.PalmettoTrialAdvocates.example</p>
</section>

<section class="envelope envelope--back">
  <svg class="envelope__flap" viewBox="0 0 444 66" aria-hidden="true">
    <path d="M0 0 H444 L436 56 Q434 64 424 64 H20 Q10 64 8 56 Z" fill="var(--flap)"/>
  </svg>
</section>

<section class="envelope envelope--front">
  <div class="wordmark"><span class="wordmark__dot"></span>The Brandwell Firm</div>
  <div class="envelope__return">
    <p>Post Office Box 4721</p>
    <p>Millbrook, SC 29555-4721</p>
  </div>
</section>

</body>
</html>
```